Business Card Design For A Cajun Seafood Restaurant

We are opening a cajun seafood restaurant in a week. We mainly serve cajun seafood which is orginally from Louisiana. We want design on both sides of a business card. I have menu on the website. You can go to www.reednkettle.example to check out our menu.

Restaurant name: Reed N' Kettle
Phone: +1 (555) 304-7712
Address: 48206 Ludlow Row, #7, Bexmoor Flats, Ca90000
Email: reednkettle@mailbox.example
Website: www.reednkettle.example

Maybe add social media icons (facebook, instagram) if looks nice on the business card.
facebook.com/reednkettle
instagram.com/reednkettle or @reednkettle

Attached is the logo and other business card samples that I like.

```html
<!DOCTYPE html>
<html lang="en">
<head>
<meta charset="utf-8">
<title>Reed N' Kettle – Business Card</title>
<link href="https://fonts.googleapis.com/css2?family=Source+Sans+3:wght@400;600;700&display=swap" rel="stylesheet">
<style>
  :root {
    --backdrop: #9b9b9b;
    --paper: #eeeeef;
    --orange: #d95a0a;
    --orange-art: #e2661e;
    --ink: #1c1c1c;
    --black: #050505;
    --white: #ffffff;
  }
  * { box-sizing: border-box; margin: 0; padding: 0; }
  html, body {
    width: 1105px; height: 1200px; overflow: hidden;
    background: var(--backdrop);
    font-family: "Source Sans 3", Arial, sans-serif;
  }
  .card {
    position: absolute; left: 182px;
    width: 746px; height: 425px;
    background: var(--paper);
    overflow: hidden;
  }
  .card--front { top: 120px; }
  .card--back { top: 637px; }

  .person { position: absolute; left: 44px; top: 58px; }
  .person__name { color: var(--orange); font-size: 27px; font-weight: 700; letter-spacing: .3px; line-height: 1; }
  .person__role { color: var(--ink); font-size: 20px; font-weight: 400; margin-top: 7px; }

  .contact-band {
    position: absolute; left: 0; top: 182px; width: 100%; height: 214px;
    background: linear-gradient(to right, var(--orange) 0 480px, var(--black) 480px);
  }
  .address { position: absolute; left: 44px; top: 36px; color: var(--white); font-size: 19px; line-height: 28px; }
  .contact-list { position: absolute; left: 44px; top: 102px; list-style: none; color: var(--white); font-size: 19px; }
  .contact-list li { display: flex; align-items: center; height: 29px; }
  .contact-list svg { width: 17px; height: 17px; margin-right: 12px; flex: none; }

  .mascot-art { position: absolute; background: var(--orange-art); border-radius: 46% 46% 40% 40%; }
  .mascot-art--front { left: 432px; top: 0; width: 221px; height: 214px; }
  .mascot-art--back { left: 290px; top: 79px; width: 166px; height: 148px; }

  .brand-name {
    position: absolute; left: 0; top: 232px; width: 100%;
    text-align: center; color: var(--ink);
    font-size: 42px; font-weight: 700; letter-spacing: 1px;
  }
  .social { position: absolute; left: 0; top: 360px; width: 100%; display: flex; justify-content: center; gap: 8px; font-size: 20px; color: var(--ink); }
  .social__item { display: flex; align-items: center; gap: 6px; }
  .social__dot { width: 27px; height: 27px; border-radius: 50%; background: var(--orange); }
</style>
</head>
<body>
  <section class="card card--front">
    <div class="person">
      <p class="person__name">DALE HARMON</p>
      <p class="person__role">CEO/Founder</p>
    </div>
    <div class="contact-band">
      <p class="address">48206 Ludlow Row, #7<br>Bexmoor Flats, Ca90000</p>
      <ul class="contact-list">
        <li>
          <svg viewBox="0 0 24 24" aria-hidden="true"><path fill="#fff" d="M6.6 10.8a15.1 15.1 0 0 0 6.6 6.6l2.2-2.2a1 1 0 0 1 1-.25 11.4 11.4 0 0 0 3.6.57 1 1 0 0 1 1 1V20a1 1 0 0 1-1 1A17 17 0 0 1 3 4a1 1 0 0 1 1-1h3.5a1 1 0 0 1 1 1c0 1.25.2 2.45.57 3.57a1 1 0 0 1-.25 1z"/></svg>
          +1 (555) 304-7712
        </li>
        <li>
          <svg viewBox="0 0 24 24" aria-hidden="true"><rect x="2" y="5" width="20" height="14" fill="#fff"/><path d="M2 5l10 8 10-8" fill="none" stroke="#d95a0a" stroke-width="1.6"/></svg>
          reednkettle@mailbox.example
        </li>
        <li>
          <svg viewBox="0 0 24 24" aria-hidden="true"><circle cx="12" cy="12" r="10" fill="#fff"/><path d="M2 12h20M12 2c3 3 3 17 0 20M12 2c-3 3-3 17 0 20" fill="none" stroke="#d95a0a" stroke-width="1.4"/></svg>
          www.reednkettle.example
        </li>
      </ul>
      <div class="mascot-art mascot-art--front" role="img" aria-label="Illustrated restaurant mascot holding corn"></div>
    </div>
  </section>

  <section class="card card--back">
    <div class="mascot-art mascot-art--back" role="img" aria-label="Illustrated restaurant mascot holding corn"></div>
    <p class="brand-name">REED N' KETTLE</p>
    <div class="social">
      <span class="social__item"><span class="social__dot"></span>reednkettle</span>
      <span class="social__item"><span class="social__dot"></span>@reednkettle</span>
    </div>
  </section>
</body>
</html>
```